Global (re)insurance broker needs a business card design

We need a classic business card for our company that is headquartered in SG, with offices in Malaysia and Dubai. We specialise in insurance and reinsurance broking and consultancy for our global clients.

```html
<!DOCTYPE html>
<html lang="en">
<head>
<meta charset="UTF-8">
<title>Korvane Business Card</title>
<link rel="stylesheet" href="https://fonts.googleapis.com/css2?family=Open+Sans:wght@400;600;700&display=swap">
<style>
  :root {
    --stage: #141416;
    --card-dark: #1f1e23;
    --brand-blue: #2d4fb2;
    --brand-green: #bcdcb6;
    --text-light: #e4e4e6;
    --text-muted: #cfcfd3;
    --deco-grey: #2b2a30;
    --back-blue: #2446a6;
    --back-blue-light: #3c62c4;
    --white: #ffffff;
  }
  * { margin: 0; padding: 0; box-sizing: border-box; }
  html, body {
    width: 1200px;
    height: 780px;
    overflow: hidden;
    background: var(--stage);
    font-family: "Open Sans", Arial, sans-serif;
  }
  .stage {
    width: 1200px;
    height: 780px;
    display: flex;
    align-items: center;
    justify-content: center;
    gap: 40px;
  }
  .card {
    position: relative;
    width: 540px;
    height: 310px;
    border-radius: 3px;
    overflow: hidden;
  }

  /* Front */
  .card-front { background: var(--card-dark); }
  .front-wordmark {
    position: absolute;
    top: 18px;
    right: 40px;
    font-size: 52px;
    font-weight: 600;
    letter-spacing: 2px;
    color: var(--brand-green);
    line-height: 1;
  }
  .contact-block {
    position: absolute;
    top: 84px;
    left: 34px;
    z-index: 1;
  }
  .person-name {
    display: flex;
    align-items: center;
    gap: 8px;
    font-size: 28px;
    font-weight: 700;
    color: var(--brand-blue);
    line-height: 1.1;
  }
  .person-name::before {
    content: "";
    width: 6px;
    height: 30px;
    background: var(--brand-green);
  }
  .person-title {
    margin: 2px 0 12px 14px;
    font-size: 15px;
    color: var(--text-muted);
  }
  .address {
    margin-left: 14px;
    font-size: 13px;
    line-height: 1.4;
    color: var(--text-light);
  }
  .contact-list {
    list-style: none;
    margin-top: 10px;
    font-size: 13px;
    line-height: 1.5;
    color: var(--text-light);
  }
  .contact-list li {
    display: flex;
    align-items: center;
    gap: 8px;
  }
  .contact-icon { width: 12px; height: 12px; flex: none; }
  .front-deco {
    position: absolute;
    right: 16px;
    bottom: 12px;
    font-size: 60px;
    font-weight: 600;
    letter-spacing: 2px;
    color: var(--deco-grey);
    line-height: 1;
  }

  /* Back */
  .card-back { background: var(--back-blue); }
  .back-pattern {
    position: absolute;
    inset: 0;
    background: linear-gradient(200deg, var(--back-blue-light) 0%, var(--back-blue) 45%, #21419c 100%);
  }
  .back-wordmark {
    position: absolute;
    left: 300px;
    top: 230px;
    font-size: 16px;
    font-weight: 600;
    letter-spacing: 1px;
    color: var(--white);
  }
</style>
</head>
<body>
<main class="stage">
  <section class="card card-front" aria-label="Business card front">
    <div class="front-wordmark">KORVANE</div>
    <div class="contact-block">
      <h1 class="person-name">Mei Lin Goh</h1>
      <p class="person-title">Chief Operating Officer</p>
      <p class="address">22 Harbour Lane, Meridian<br>Tower #08-04, Singapore 048621</p>
      <ul class="contact-list">
        <li>
          <svg class="contact-icon" viewBox="0 0 12 12" aria-hidden="true"><rect x="3" y="0.5" width="6" height="11" rx="1" fill="none" stroke="#cfcfd3"/></svg>
          +65 8123 4567
        </li>
        <li>
          <svg class="contact-icon" viewBox="0 0 12 12" aria-hidden="true"><circle cx="6" cy="6" r="5.5" fill="#2d4fb2"/><path d="M0.5 6h11M6 0.5c-2.5 3-2.5 8 0 11M6 0.5c2.5 3 2.5 8 0 11" fill="none" stroke="#1f1e23" stroke-width="0.8"/></svg>
          www.korvane.com
        </li>
        <li>
          <svg class="contact-icon" viewBox="0 0 12 12" aria-hidden="true"><rect x="0.5" y="2" width="11" height="8" fill="none" stroke="#bcdcb6"/><path d="M0.5 2l5.5 4.5L11.5 2" fill="none" stroke="#bcdcb6"/></svg>
          meilin@korvane.com
        </li>
      </ul>
    </div>
    <div class="front-deco" aria-hidden="true">KORVANE</div>
  </section>

  <section class="card card-back" aria-label="Business card back">
    <div class="back-pattern" role="img" aria-label="Repeating company name pattern in blue tones"></div>
    <div class="back-wordmark">KORVANE</div>
  </section>
</main>
</body>
</html>
```